New Business Card Design for Manufacturing

We are an engineering/manufacturing company that offers Advanced machining/assembly/engineering services, as well as innovative products for the heavy duty engine cooling markets.

We are looking to get a new business card designed that is clean and modern looking, but still fits the wide range of technical/skilled work we do.

- We hope to use this design as the base for other design work in new Presentations, web, and print work.

Industry/Entity Type

Engineering

Contact Information for Business Card

Our preferred color of blue is (RGB) 22/71/159 but can vary slightly from that color. Our content will be our Logo and full company name (Vantrell Forge Works, Inc.), company address, name, job title, phone number with extension, cell number, fax number, website, and email address on the cards.
We'd like the full company name next to the logo, but we are open to other interpretations of that layout.
Preferably, we would like the back side to be clean with just our logo, and the front to contain all of the contact information.

Colors
2f74b4
0355a3
85abd2

Requirements
Must have
• - Logo, company name, needed content - We are open to interpretation beyond that.
• - Standard size business card.
• - Horizontal orientation.
• - Enough space for lengthy names / job titles (for example, a job title could read "Directory of Human Resources" or "V.P. of Governmental Affairs"). We need this to look clean, whether the title be short (CEO) or long (as described above).

```html
<!DOCTYPE html>
<html lang="en">
<head>
<meta charset="utf-8">
<title>Vantrell Forge Works – Business Card</title>
<link href="https://fonts.googleapis.com/css2?family=Open+Sans:wght@400;600;700&display=swap" rel="stylesheet">
<style>
  :root {
    --stage: #2b2b2d;
    --card: #0b0b0c;
    --card-edge: #1c1c1f;
    --blue: #2f74b4;
    --blue-deep: #0355a3;
    --blue-light: #85abd2;
    --text: #e9e9ea;
    --muted: #9a9ca1;
  }
  * { box-sizing: border-box; margin: 0; padding: 0; }
  html, body {
    width: 1200px; height: 896px; overflow: hidden;
    background: var(--stage);
    font-family: "Open Sans", Arial, sans-serif;
  }
  .stage {
    position: relative; width: 1200px; height: 896px;
    display: flex; align-items: center; justify-content: center; gap: 50px;
  }
  .card {
    position: relative; width: 525px; height: 300px;
    background: linear-gradient(160deg, var(--card-edge) 0%, var(--card) 45%, #000 100%);
    border-radius: 18px; overflow: hidden;
    box-shadow: 0 18px 40px rgba(0,0,0,.55);
    color: var(--text);
  }
  .card__band {
    position: absolute; left: 0; right: 0; bottom: 22px; height: 16px;
    background: linear-gradient(90deg, var(--blue-deep), var(--blue), var(--blue-light));
  }

  /* Back */
  .brand-mark { position: absolute; left: 120px; top: 88px; }
  .brand-mark__name {
    display: flex; align-items: center; gap: 10px;
    font-size: 30px; font-weight: 700; color: var(--blue); letter-spacing: .5px;
  }
  .brand-mark__square { width: 18px; height: 18px; background: var(--blue); flex: none; }
  .brand-mark__tagline {
    margin-top: 6px; margin-left: 28px;
    font-size: 14px; font-weight: 600; color: var(--muted); letter-spacing: 1.5px; text-transform: uppercase;
  }
  .back__web {
    position: absolute; left: 148px; top: 196px;
    font-size: 15px; color: var(--text);
  }
  .back__web span { color: var(--blue); }

  /* Front */
  .front__logo { position: absolute; left: 30px; top: 34px; }
  .front__logo .brand-mark__name { font-size: 15px; gap: 7px; line-height: 1.15; align-items: flex-start; }
  .front__logo .brand-mark__square { width: 11px; height: 11px; margin-top: 3px; }
  .front__logo .brand-mark__tagline { font-size: 8.5px; margin-left: 18px; margin-top: 4px; letter-spacing: 1px; }
  .front__accent {
    position: absolute; right: 0; top: 26px; width: 46px; height: 10px;
    background: var(--blue);
  }
  .front__accent::before {
    content: ""; position: absolute; left: -6px; top: 0; width: 3px; height: 10px; background: var(--muted);
  }
  .person { position: absolute; right: 40px; top: 48px; text-align: right; }
  .person__name { font-size: 22px; color: var(--blue); letter-spacing: .5px; text-transform: uppercase; }
  .person__title { font-size: 12.5px; color: var(--text); margin-top: 2px; }
  .front__rule {
    position: absolute; left: 30px; right: 40px; top: 112px; height: 1px; background: var(--blue);
  }
  .address {
    position: absolute; right: 40px; top: 128px; text-align: right;
    font-style: normal; font-size: 12.5px; line-height: 1.55; color: var(--text);
  }
  .contacts {
    position: absolute; left: 30px; top: 160px; list-style: none;
    font-size: 13px; line-height: 1.6; color: var(--text);
  }
  .contacts li { display: flex; align-items: center; gap: 8px; }
  .contacts svg { width: 10px; height: 10px; fill: var(--blue); flex: none; }
  .contacts .hl { color: var(--blue); }
</style>
</head>
<body>
<main class="stage">
  <section class="card card--back" aria-label="Card back">
    <div class="brand-mark">
      <div class="brand-mark__name"><span class="brand-mark__square"></span>Vantrell Forge Works</div>
      <div class="brand-mark__tagline">Built to Endure</div>
    </div>
    <p class="back__web">www.<span>vantrellforge</span>.com</p>
    <div class="card__band"></div>
  </section>

  <section class="card card--front" aria-label="Card front">
    <div class="brand-mark front__logo">
      <div class="brand-mark__name"><span class="brand-mark__square"></span><span>Vantrell Forge<br>Works, Inc.</span></div>
      <div class="brand-mark__tagline">Built to Endure</div>
    </div>
    <div class="front__accent"></div>
    <div class="person">
      <p class="person__name">Mara Ellison</p>
      <p class="person__title">Directory of Human Resources</p>
    </div>
    <div class="front__rule"></div>
    <address class="address">418 Calder Ave., Ste. 210<br>Harlow Falls, ST 00000 USA</address>
    <ul class="contacts">
      <li><svg viewBox="0 0 10 10"><path d="M2 0l2 2-1 1.5c.6 1.3 1.6 2.3 2.5 2.5L7 5l3 2-1 2c-5 0-9-4-9-9z"/></svg><span>(555) 014-8822</span></li>
      <li><svg viewBox="0 0 10 10"><path d="M0 2h10v6H0zM1 3v.4l4 2.6 4-2.6V3z"/></svg><span>info@vantrellforge.com</span></li>
      <li><svg viewBox="0 0 10 10"><circle cx="5" cy="5" r="5"/></svg><span>www.<span class="hl">vantrellforge</span>.com</span></li>
    </ul>
    <div class="card__band"></div>
  </section>
</main>
</body>
</html>
```